Business Cards for Volmont Hayes, a law firm

We changed our firm's name from "Volmont & Hayes LLP" to "Volmont Hayes", we need to update our cards with a new design. We like the overall look of the back but the front side of the cards (see attached mockup) needs a refreshed look. I also attach our current logo so you can get rid of that LLP and &. We have a new address as well (not same as on mockup).

Target Market(s)

Clients of law firm

Industry/Entity Type

Law Firm

Contact Information for Business Card

Frontsides:

Lorenzo T. Volmont
Partner
Tel: (416) 555-0172 ext. 101
Fax: (647) 555-0139
Email: lvolmont@vhlegal.example

Simon P. Hayes
Partner
Tel: (416) 555-0172 ext. 102
Fax: (647) 555-0139
Email: simonhayes@vhlegal.example

Mark E. Dorsan
Barrister
Tel: (416) 555-0172 ext. 104
Fax: (647) 555-0139
Email: mdorsan@vhlegal.example

The back side should be crimson red (see mockup) with the logo (please update it to remove the & and the LLP, you can modify it a bit to make it tasteful if need be). Our new address is

82 Marlow Rd W, Suite 710
Toronto, ON M5K 0Z9

After our address, please also include our website www.vhlegal.example

Font styles to use
Sans Serif

Colors
ec2027
ffffff
000000

Requirements
Must have
• PLEASE NOTE: our firm's colour is more of a darker/crimson red, not a vibrant red.
• The front should have space for the lawyer's name, title, phone number (with extension), fax number, and email.
• If you're going to add those yourself, the info for the frontside is in the "Business Card Details" section (three lawyers that need their own cards).
Nice to have
• We like the backside of our current cards, just update it with our new address (one address now instead of 2), and a slightly modified logo (not a new logo altogether).
• The frontside should be refreshed with a better look (think minimalist, professional and modern), although still predominantly white-based background.
Should not have
• No scales of justice or other cheesy lawyer stereotype symbols! :-)

```html
<!DOCTYPE html>
<html lang="en">
<head>
<meta charset="utf-8">
<title>Volmont Hayes – Business Card Concepts</title>
<link rel="stylesheet" href="https://fonts.googleapis.com/css2?family=Hind:wght@400;500;600;700&display=swap">
<style>
  :root {
    --page: #f2f2f2;
    --crimson: #c41e14;
    --red-bright: #e13d3a;
    --red-accent: #e3262a;
    --charcoal: #333333;
    --white: #ffffff;
    --ink: #111111;
    --pattern-tone: #f6f6f6;
    --rule-dark: rgba(0, 0, 0, 0.55);
  }
  * { box-sizing: border-box; margin: 0; padding: 0; }
  html, body {
    width: 1200px;
    height: 978px;
    overflow: hidden;
    background: var(--page);
    font-family: "Hind", Arial, sans-serif;
  }
  .sheet { position: relative; width: 1200px; height: 978px; }

  .card {
    position: absolute;
    width: 561px;
    height: 280px;
    overflow: hidden;
  }
  .card--back { left: 24px; }
  .card--front {
    left: 608px;
    background: var(--white);
    box-shadow: 0 1px 4px rgba(0, 0, 0, 0.18);
  }
  .row-1 { top: 48px; }
  .row-2 { top: 353px; }
  .row-3 { top: 658px; }

  /* Back side */
  .back--crimson { background: var(--crimson); }
  .back--red { background: var(--red-bright); }
  .back--charcoal { background: var(--charcoal); }

  .back__brand {
    position: absolute;
    top: 118px;
    left: 0;
    width: 100%;
    text-align: center;
    font-size: 34px;
    font-weight: 700;
    color: var(--white);
    letter-spacing: 0.2px;
  }
  .back__rule {
    position: absolute;
    top: 200px;
    left: 0;
    width: 100%;
    height: 2px;
    background: var(--rule-dark);
  }
  .back--charcoal .back__rule { background: rgba(255, 255, 255, 0.75); height: 1px; }
  .back__address {
    position: absolute;
    top: 223px;
    left: 24px;
    font-size: 11.5px;
    font-weight: 600;
    line-height: 17px;
    color: var(--white);
  }
  .back__web {
    position: absolute;
    top: 231px;
    right: 24px;
    font-size: 12.5px;
    font-weight: 600;
    color: var(--white);
  }

  /* Front side */
  .front__pattern {
    position: absolute;
    inset: 0;
    background: var(--pattern-tone);
  }
  .front__brand {
    position: absolute;
    top: 86px;
    right: 38px;
    font-size: 19px;
    font-weight: 700;
    color: var(--red-accent);
  }
  .front__name {
    position: absolute;
    top: 110px;
    left: 31px;
    font-size: 14.5px;
    font-weight: 700;
    color: var(--red-accent);
    letter-spacing: 0.3px;
  }
  .front__title {
    position: absolute;
    top: 130px;
    left: 31px;
    font-size: 12.5px;
    color: var(--red-accent);
  }
  .front__contact {
    position: absolute;
    top: 199px;
    left: 31px;
    font-size: 12.5px;
    line-height: 17px;
    color: var(--ink);
    letter-spacing: 0.3px;
  }
  .front__contact b { font-weight: 700; }
  .front__rule {
    position: absolute;
    top: 201px;
    left: 0;
    width: 100%;
    height: 1.5px;
    background: var(--ink);
  }
  .front__contact--split { top: 226px; }
  .front__email-right {
    position: absolute;
    top: 226px;
    left: 317px;
    font-size: 12.5px;
    color: var(--ink);
    letter-spacing: 0.3px;
  }
</style>
</head>
<body>
<main class="sheet">

  <!-- Row 1 -->
  <section class="card card--back back--crimson row-1">
    <div class="back__brand">VolmontHayes</div>
    <div class="back__rule"></div>
    <div class="back__address">82 Marlow Rd W, Suite 710<br>Toronto, ON M5K 0Z9</div>
    <div class="back__web">www.vhlegal.example</div>
  </section>
  <section class="card card--front row-1">
    <div class="front__brand">VolmontHayes</div>
    <div class="front__name">Lorenzo T. Volmont</div>
    <div class="front__title">Partner</div>
    <div class="front__contact">
      <b>Tel:</b> (416) 555-0172 ext. 101<br>
      <b>Fax:</b> (647) 555-0139<br>
      <b>Email:</b> lvolmont@vhlegal.example
    </div>
  </section>

  <!-- Row 2 -->
  <section class="card card--back back--red row-2">
    <div class="back__brand">VolmontHayes</div>
    <div class="back__rule"></div>
    <div class="back__address">82 Marlow Rd W, Suite 710<br>Toronto, ON M5K 0Z9</div>
    <div class="back__web">www.vhlegal.example</div>
  </section>
  <section class="card card--front row-2">
    <div class="front__pattern" role="img" aria-label="Faint repeating brand pattern across the card background"></div>
    <div class="front__brand">VolmontHayes</div>
    <div class="front__name">Lorenzo T. Volmont</div>
    <div class="front__title">Partner</div>
    <div class="front__contact">
      <b>Tel:</b> (416) 555-0172 ext. 101<br>
      <b>Fax:</b> (647) 555-0139<br>
      <b>Email:</b> lvolmont@vhlegal.example
    </div>
  </section>

  <!-- Row 3 -->
  <section class="card card--back back--charcoal row-3">
    <div class="back__brand">VolmontHayes</div>
    <div class="back__rule"></div>
    <div class="back__address">82 Marlow Rd W, Suite 710<br>Toronto, ON M5K 0Z9</div>
    <div class="back__web">www.vhlegal.example</div>
  </section>
  <section class="card card--front row-3">
    <div class="front__brand">VolmontHayes</div>
    <div class="front__name">Lorenzo T. Volmont</div>
    <div class="front__title">Partner</div>
    <div class="front__rule"></div>
    <div class="front__contact front__contact--split">
      <b>Tel:</b> (416) 555-0172 ext. 101<br>
      <b>Fax:</b> (647) 555-0139
    </div>
    <div class="front__email-right"><b>Email:</b> lvolmont@vhlegal.example</div>
  </section>

</main>
</body>
</html>
```